Chartered Professional Accounting Firm Needs a Business Card Design

We need a card design for an accounting firm based in Toronto, Ontario. The firm name is Pavel Ostrom Professional Corporation. The owner of the firm is a chartered professional accountant and a certified general accountant. Services of the firm include 60% tax preparation and consulting and 40% financial statements for corporation year-end. We would like a modern design. The color could be black, white, gray, blue or other color to bring more confidence to clients. The logo of the firm should be included in the design. Thanks

Name: Pavel Ostrom, CPA, CGA Address: 47 Maple Crest Rd. Richmond Hill, ON L7K 3B5 Telephone: (416) 562-3907 Fax:(416) 734-2165 Email: pavel@pavelostrom-example.ca

Accounting

```html
<!DOCTYPE html>
<html lang="en">
<head>
<meta charset="utf-8">
<title>Pavel Ostrom Professional Corporation — Business Card</title>
<link href="https://fonts.googleapis.com/css2?family=Cinzel:wght@400;600;700&display=swap" rel="stylesheet">
<style>
  :root {
    --page-bg: #e9e9ec;
    --card-blue-light: #3338a8;
    --card-blue-dark: #1b1f72;
    --panel-white: #f7f7f8;
    --panel-edge: #c9c9cf;
    --brand-blue: #2b3290;
    --brand-gray: #8a8a92;
    --card-text: #eef0fa;
    --rule: rgba(238, 240, 250, 0.45);
  }
  * { margin: 0; padding: 0; box-sizing: border-box; }
  html, body {
    width: 1200px;
    height: 900px;
    overflow: hidden;
    background: var(--page-bg);
  }
  .canvas {
    position: relative;
    width: 1200px;
    height: 900px;
  }
  .business-card {
    position: absolute;
    left: 100px;
    top: 165px;
    width: 1000px;
    height: 570px;
    overflow: hidden;
    background: linear-gradient(135deg, var(--card-blue-light) 0%, var(--card-blue-dark) 100%);
    box-shadow: 0 18px 40px rgba(0, 0, 0, 0.22);
    font-family: "Cinzel", serif;
  }
  .white-panel {
    position: absolute;
    inset: 0;
    width: 1000px;
    height: 570px;
  }
  .brand-block {
    position: absolute;
    left: 40px;
    top: 230px;
    width: 330px;
    text-align: center;
    color: var(--brand-blue);
  }
  .brand-name {
    display: flex;
    align-items: center;
    justify-content: center;
    gap: 12px;
    font-size: 34px;
    font-weight: 700;
    letter-spacing: 1px;
    line-height: 1;
  }
  .brand-square {
    width: 26px;
    height: 26px;
    background: var(--brand-blue);
    flex: none;
  }
  .brand-sub {
    margin-top: 8px;
    font-size: 17px;
    font-weight: 700;
    letter-spacing: 1.5px;
  }
  .brand-credentials {
    margin-top: 8px;
    font-size: 12.5px;
    font-weight: 400;
    line-height: 1.45;
    letter-spacing: 1px;
    color: var(--brand-gray);
  }
  .contact-block {
    position: absolute;
    left: 450px;
    top: 170px;
    color: var(--card-text);
  }
  .holder-name {
    font-size: 34px;
    font-weight: 600;
    letter-spacing: 1px;
    padding-bottom: 12px;
    border-bottom: 1px solid var(--rule);
    width: 480px;
  }
  .contact-lines {
    list-style: none;
    margin-top: 16px;
    margin-left: 24px;
    font-size: 19px;
    line-height: 1.75;
    letter-spacing: 0.8px;
  }
  .address {
    position: absolute;
    left: 440px;
    top: 478px;
    font-size: 16px;
    letter-spacing: 0.8px;
    color: var(--card-text);
  }
</style>
</head>
<body>
<main class="canvas">
  <section class="business-card" aria-label="Business card for Pavel Ostrom Professional Corporation">
    <svg class="white-panel" viewBox="0 0 1000 570" aria-hidden="true">
      <path d="M0,0 H345 C395,140 420,380 385,570 H0 Z" fill="var(--panel-edge)"/>
      <path d="M0,0 H330 C378,140 402,380 368,570 H0 Z" fill="var(--panel-white)"/>
    </svg>

    <div class="brand-block">
      <div class="brand-name"><span class="brand-square"></span>Pavel Ostrom</div>
      <div class="brand-sub">Professional Corporation</div>
      <div class="brand-credentials">
        Chartered Professional Accountant<br>
        Certified General Accountant
      </div>
    </div>

    <div class="contact-block">
      <h1 class="holder-name">Pavel Ostrom, CPA, CGA</h1>
      <ul class="contact-lines">
        <li>Telephone: (416) 562-3907</li>
        <li>Fax: (416) 734-2165</li>
        <li>Email: pavel@pavelostrom-example.ca</li>
      </ul>
    </div>

    <p class="address">47 Maple Crest Rd. Richmond Hill, ON L7K 3B5</p>
  </section>
</main>
</body>
</html>
```